Toms welding and seed cleaning Business cards

Jakes welding and seed cleaningWe clean wheat seed on farm with portable cleaners so the farmers have pure wheat seed to plant back for the next crop. We are certified to clean foundation, registered, and certified seed wheat. Our cleaners being portable make it easier for the farmers because we do it right on there farm so they don't have to haul it all to townWhen there is no wheat to clean we weld in the winter. We improve, add onto, and build new corrals. We also build sheds, cattle shelters, and wind breaks. Other welding is welcomed

Reason: I need to extend the deadline because I've been busy and not had my game together. I need more time figure out what I want yet

Industry/Entity Type

Agriculture

Contact Information for Business Card

Just "toms welding and seed cleaning" on front and other info on the back
On the back side I would like to have my address.
Morris Tulane
48213 W COUNTY RD 318
ISABELLA OK 73747
Phone #5804419362

Font styles to use
Sans Serif

Requirements
Must have
• list we are certified to clean foundation, registered, and certified wheat
• State that they are portable cleaners
• For the welding part list, add on to, improve on, and repair existing corrals and new corrals and other welding welcomed
Nice to have
• A wheat field with some metal corrals on the side with a nice classic looking barn for a background. Maybe some cattle in the corrals
• A nice looking farm yard would be good too

```html
<!DOCTYPE html>
<html lang="en">
<head>
<meta charset="utf-8">
<title>Toms Welding And Seed Cleaning – Business Cards</title>
<link href="https://fonts.googleapis.com/css2?family=Montserrat:wght@400;700&family=PT+Sans+Narrow:wght@400;700&display=swap" rel="stylesheet">
<style>
  :root {
    --canvas: #ffffff;
    --ink: #111111;
    --pill: #000000;
    --title-yellow: #ffec00;
    --body-white: #ffffff;
    --brown-deep: #2a1407;
    --brown-mid: #6b3e1c;
    --brown-glow: #a8774a;
    --spark-dark: #140c08;
    --spark-glow: #c7702a;
    --wheat-sky: #e8a23a;
    --wheat-field: #b8772b;
    --wheat-dark: #6e4414;
  }
  * { margin: 0; padding: 0; box-sizing: border-box; }
  html, body {
    width: 1200px; height: 1000px; overflow: hidden;
    background: var(--canvas);
  }
  .canvas { position: relative; width: 1200px; height: 1000px; }

  /* Front card */
  .card-front {
    position: absolute; left: 229px; top: 93px; width: 736px; height: 400px;
    overflow: hidden;
  }
  .photo-welding {
    position: absolute; left: 0; top: 0; width: 371px; height: 400px;
    background:
      radial-gradient(circle at 78% 62%, #ffd77a 0%, var(--spark-glow) 8%, rgba(120,60,20,.5) 22%, transparent 45%),
      linear-gradient(160deg, var(--spark-dark) 0%, #2b1a10 60%, #4a2e1a 100%);
  }
  .photo-wheat {
    position: absolute; left: 371px; top: 0; width: 365px; height: 400px;
    background:
      radial-gradient(circle at 53% 27%, #fff6c8 0%, #ffc54a 6%, rgba(230,140,40,.6) 20%, transparent 42%),
      linear-gradient(180deg, #5a2e0c 0%, var(--wheat-sky) 30%, var(--wheat-field) 45%, var(--wheat-dark) 100%);
  }
  .front-name {
    position: absolute; left: 43px; top: 320px; width: 646px; height: 54px;
    background: var(--pill); border-radius: 27px;
    color: var(--body-white);
    font-family: "PT Sans Narrow", sans-serif; font-size: 42px; line-height: 54px;
    text-align: center; letter-spacing: 0.2px;
  }

  /* Back card */
  .card-back {
    position: absolute; left: 234px; top: 528px; width: 734px; height: 398px;
    overflow: hidden; border: 1px solid #6a4a33;
    background:
      radial-gradient(ellipse at 22% 35%, var(--brown-glow) 0%, var(--brown-mid) 30%, transparent 65%),
      linear-gradient(180deg, var(--brown-deep) 0%, var(--brown-mid) 55%, var(--brown-deep) 100%);
  }
  .back-title {
    position: absolute; left: 20px; top: 12px;
    color: var(--title-yellow);
    font-family: "Montserrat", sans-serif; font-weight: 700; font-size: 27px;
    letter-spacing: 0.3px;
  }
  .service-list {
    position: absolute; left: 26px; top: 58px; width: 700px;
    list-style: none;
    color: var(--body-white);
    font-family: "Montserrat", sans-serif; font-size: 16px; line-height: 19.5px;
  }
  .service-list li { margin-bottom: 19px; padding-left: 12px; text-indent: -12px; }
  .service-list li::before { content: "* "; }
  .footer-edge { position: absolute; left: 0; top: 0; }
  .contact {
    position: absolute; left: 14px;
    color: var(--ink);
    font-family: "Montserrat", sans-serif; font-size: 13.5px;
  }
  .contact-address { top: 346px; }
  .contact-phone { top: 370px; }
  .back-tag {
    position: absolute; right: 0; bottom: 0; width: 288px; height: 28px;
    background: var(--pill);
    clip-path: polygon(14px 0, 100% 0, 100% 100%, 14px 100%, 0 50%);
    color: var(--body-white);
    font-family: "PT Sans Narrow", sans-serif; font-weight: 700; font-size: 20px;
    line-height: 28px; text-align: right; padding-right: 6px;
  }
</style>
</head>
<body>
<main class="canvas">

  <section class="card-front">
    <div class="photo-welding" role="img" aria-label="Welder cutting metal with a torch, sparks flying"></div>
    <div class="photo-wheat" role="img" aria-label="Golden wheat field at sunset with birds in the sky"></div>
    <div class="front-name">Toms Welding And Seed Cleaning</div>
  </section>

  <section class="card-back">
    <h1 class="back-title">At Toms welding and seed cleaning...</h1>
    <ul class="service-list">
      <li>We use portable cleaners to clean your wheat seed&nbsp; so that you are ready to plant the pure wheat seed for the next crop.</li>
      <li>You can get the cleaning done on your farms instead of hauling<br>it over to town.</li>
      <li>We are registered and certified professionals.</li>
      <li>&nbsp;We improve and build new corrals in winters.</li>
      <li>&nbsp;We can help you build sheds, cattle shelters, wind breaks, etc.</li>
      <li>&nbsp;Other welding jobs are also welcomed.</li>
    </ul>
    <svg class="footer-edge" width="734" height="398" viewBox="0 0 734 398" aria-hidden="true">
      <polygon fill="#ffffff" points="0,334 150,326 330,340 480,330 560,336 640,328 700,324 734,332 734,398 0,398"/>
    </svg>
    <p class="contact contact-address">Address: xyz xyz xyz 0000 zyx xyzxxxx yyyyyy zzzzzz xxxxxxx yyyyy zzzzzz</p>
    <p class="contact contact-phone">Call Us at 000-00-000&nbsp; Email: xyz@xyz.com</p>
    <div class="back-tag">Toms Welding And Seed Cleaning</div>
  </section>

</main>
</body>
</html>
```